Les Brumevents

I need a book cover for an action series. Two books are already on sale, but the covers have been rejected by some online booksellers for having a shirtless man on the cover.
https://www.bookvane.com/dp/Q58KT2R7WX

The Bookvane pages give descriptions of the book. I'm taking bids on modification of the first book, but the intention would be to use the same designer for the series.

Timeline for delivery is ideally end of Q1 22 for cover

My goal for the coves is for the reader to see some kind of "hook" that makes them intrigued enough to click the link. The cover will need to convey the genre of the book (action thriller) and give the potential buyer a reason to click for more information. Some online booksellers only show cover and title, so the cover needs to sell the book.

The actual gender split in the mystery-thriller field has faded, and the cover shouldn't just appeal to men although the gender spilt is still 60-40 towards male readership.

In the initial design, I was attempting to use country/continental outlines to convey as sense of "International Thriller", as the main character is an ex-French Foreign Legionnaire.

I would like to prioritize these elements:
Title
Series Name & Number

The author name doesn't need to be prominent or even on the front cover. Back cover copy is available, on the Bookvane description, but I can resend as text.

Target Market(s)

Requirements
Must have
• Title & Series Name & Number
Should not have
• Nudity, or explicit sexual content

```html
<!DOCTYPE html>
<html lang="fr">
<head>
<meta charset="utf-8">
<title>Sahelian Exfiltration – Les Brumevents – cover spread</title>
<link rel="stylesheet" href="https://fonts.googleapis.com/css2?family=Teko:wght@500;600&family=Open+Sans:wght@400;700&display=swap">
<style>
  :root {
    --page: #ffffff;
    --cover: #050505;
    --spine: #0a0a0a;
    --title-red: #c8161d;
    --ink-white: #f4f4f4;
    --photo-light: #8a8a8a;
    --photo-mid: #3a3a3a;
    --photo-dark: #0b0b0b;
  }
  * { margin: 0; padding: 0; box-sizing: border-box; }
  html, body {
    width: 1200px; height: 288px; overflow: hidden;
    background: var(--page);
  }
  .spread {
    position: absolute; left: 390px; top: 0;
    width: 420px; height: 288px;
    background: var(--cover);
    font-family: "Teko", "Arial Narrow", sans-serif;
    color: var(--ink-white);
  }
  .back-cover { position: absolute; left: 0; top: 0; width: 192px; height: 288px; }
  .spine { position: absolute; left: 192px; top: 0; width: 35px; height: 288px; background: var(--spine); }
  .front-cover { position: absolute; left: 227px; top: 0; width: 193px; height: 288px; }

  .series-name { color: var(--title-red); font-weight: 600; line-height: 1; text-align: center; white-space: nowrap; }
  .series-word { font-weight: 600; line-height: 1; text-align: center; white-space: nowrap; }
  .book-title { font-weight: 600; line-height: 1; text-align: center; white-space: nowrap; }

  /* back cover */
  .back-cover .series-name { position: absolute; top: 35px; width: 100%; font-size: 27px; left: 4px; }
  .back-cover .series-word { position: absolute; top: 60px; width: 100%; font-size: 15px; left: 4px; }
  .back-cover .book-title { position: absolute; top: 76px; width: 100%; font-size: 17px; left: 4px; }
  .blurb {
    position: absolute; left: 18px; width: 156px;
    font-family: "Open Sans", Arial, sans-serif;
    font-size: 5.6px; line-height: 8.9px;
    text-align: justify; text-align-last: center;
  }
  .blurb-first { top: 99px; }
  .blurb-second { top: 179px; }

  /* spine */
  .spine-titles {
    position: absolute; top: 16px; right: 4px; height: 148px;
    writing-mode: vertical-rl;
    font-weight: 600; line-height: 0.95;
    white-space: nowrap;
  }
  .spine-titles .spine-series { font-size: 15px; display: block; }
  .spine-titles .spine-series .red { color: var(--title-red); }
  .spine-titles .spine-book { font-size: 10px; font-weight: 500; display: block; }
  .spine-author {
    position: absolute; top: 175px; left: 13px;
    writing-mode: vertical-rl;
    font-family: "Open Sans", Arial, sans-serif; font-weight: 700;
    font-size: 10px; letter-spacing: 1.6px;
    white-space: nowrap;
  }

  /* front cover */
  .cover-photo { position: absolute; left: 18px; top: 98px; width: 160px; height: 128px; }
  .front-cover .series-name { position: absolute; top: 32px; width: 100%; font-size: 43px; }
  .front-cover .series-word { position: absolute; top: 72px; width: 100%; font-size: 24px; }
  .front-cover .book-title { position: absolute; top: 228px; width: 100%; font-size: 27px; }
  .author-name {
    position: absolute; top: 257px; width: 100%; text-align: center;
    font-family: "Open Sans", Arial, sans-serif; font-weight: 700;
    font-size: 11.5px; letter-spacing: 1.3px;
    white-space: nowrap;
  }
</style>
</head>
<body>
<main class="spread">
  <section class="back-cover">
    <h2 class="series-name">SAHELIAN</h2>
    <p class="series-word">EXFILTRATION</p>
    <p class="book-title">LES BRUMEVENTS</p>
    <p class="blurb blurb-first">Ex-legionnaire Marc Delaunay wanted a quiet life far from war. When a convoy of aid workers vanishes on a desert road, an old comrade calls in a debt. With a small team of retired fighters, he crosses borders no one else will cross, racing a ruthless warlord before time runs out.</p>
    <p class="blurb blurb-second">The mission should take three days. It takes everything they have. Betrayed by the people who hired them and hunted across hostile ground, the retirees must decide who to trust and how far they will go to bring every hostage home alive. Some debts can only be paid in full.</p>
  </section>

  <section class="spine">
    <div class="spine-titles">
      <span class="spine-series"><span class="red">SAHELIAN</span> EXFILTRATION</span>
      <span class="spine-book">LES BRUMEVENTS</span>
    </div>
    <div class="spine-author">JON HARLOWE</div>
  </section>

  <section class="front-cover">
    <svg class="cover-photo" role="img" aria-label="Black and white photograph of two clenched fists bound together with rope" viewBox="0 0 160 128" preserveAspectRatio="none">
      <defs>
        <radialGradient id="photoTone" cx="50%" cy="45%" r="55%">
          <stop offset="0%" stop-color="var(--photo-light)"/>
          <stop offset="55%" stop-color="var(--photo-mid)"/>
          <stop offset="100%" stop-color="var(--photo-dark)"/>
        </radialGradient>
      </defs>
      <rect width="160" height="128" fill="url(#photoTone)"/>
    </svg>
    <h1 class="series-name">SAHELIAN</h1>
    <p class="series-word">EXFILTRATION</p>
    <p class="book-title">LES BRUMEVENTS</p>
    <p class="author-name">JON HARLOWE</p>
  </section>
</main>
</body>
</html>
```